Sunscreen Package Design Modern SPF 50

Update current package design to a more modern design target women 16-40 Do not make it playful. Calden Cove is home to movie stars and high income business people PalmSprings is one of the most desired vacation areas in the world. The sun shines 350 days a year. World class Tennis and Golf tournaments are held every year with the worlds top players attending these tournaments

Target Market(s)

Women

Industry/Entity Type

Skin Protection

Font styles to use
Sans Serif

Requirements
Must have
• The words Calden Cove and KORIVELL

```html
<!DOCTYPE html>
<html lang="en">
<head>
<meta charset="utf-8">
<title>Calden Cove Korivell AfterSun Label</title>
<link rel="stylesheet" href="https://fonts.googleapis.com/css2?family=Manrope:wght@400;500;600;700;800&display=swap">
<style>
  :root {
    --sand: #f0e2d7;
    --teal: #53c8d4;
    --teal-soft: #a9d9d8;
    --foam: #c8ddd6;
    --ink: #1f2b2e;
    --white: #ffffff;
  }
  * { margin: 0; padding: 0; box-sizing: border-box; }
  html, body { width: 1028px; height: 1200px; overflow: hidden; background: var(--white); }
  body { position: relative; font-family: "Manrope", sans-serif; color: var(--ink); }

  .front-panel {
    position: absolute; left: 73px; top: 64px; width: 409px; height: 1039px;
    background: var(--sand); overflow: hidden;
  }
  .front-panel .waves { position: absolute; left: 0; top: 0; width: 409px; height: 1039px; }

  .brand-dot {
    position: absolute; left: 170px; top: 90px; width: 70px; height: 70px;
    border-radius: 50%; background: var(--teal);
  }
  .brand-name {
    position: absolute; left: 0; top: 250px; width: 409px; text-align: center;
    font-weight: 700; font-size: 50px; letter-spacing: 4px; line-height: 64px;
    color: var(--ink);
  }

  .product-title {
    position: absolute; left: 0; top: 510px; width: 409px; text-align: center;
    color: var(--white); font-weight: 800; font-size: 44px; letter-spacing: 8px; line-height: 56px;
  }
  .tagline {
    position: absolute; left: 0; top: 598px; width: 409px; text-align: center;
    font-size: 18px; font-weight: 500; line-height: 31px; letter-spacing: -0.3px;
  }
  .ingredient-pill {
    position: absolute; height: 39px; border: 1px solid var(--ink); border-radius: 9px;
    display: flex; align-items: center; justify-content: center; gap: 7px;
    font-size: 13px; font-weight: 500; letter-spacing: -0.2px;
  }
  .ingredient-pill .icon { width: 11px; height: 11px; border-radius: 50%; background: var(--ink); flex: none; }
  .volume {
    position: absolute; left: 0; top: 848px; width: 409px; text-align: center;
    color: var(--white); font-weight: 700; font-size: 20px; line-height: 26px;
  }

  .back-panel {
    position: absolute; left: 541px; top: 66px; width: 409px; height: 1040px;
    background: var(--teal); overflow: hidden;
  }
  .copy-block {
    position: absolute; left: 27px; width: 358px;
    font-size: 12px; line-height: 14px; letter-spacing: -0.2px; font-weight: 400;
  }
  .copy-heading {
    position: absolute; left: 28px; font-size: 13.5px; font-weight: 700; line-height: 16px;
  }
</style>
</head>
<body>

<section class="front-panel">
  <svg class="waves" viewBox="0 0 409 1039" aria-hidden="true">
    <path d="M0 425 C 90 455, 160 445, 250 430 C 320 420, 370 425, 409 440 L409 1039 L0 1039 Z" fill="var(--foam)"/>
    <path d="M0 440 C 90 472, 170 462, 255 448 C 325 437, 372 445, 409 462 L409 1039 L0 1039 Z" fill="var(--teal-soft)"/>
    <path d="M0 442 C 90 482, 175 478, 260 462 C 330 450, 375 458, 409 478 L409 1039 L0 1039 Z" fill="var(--teal)"/>
    <path d="M0 930 C 80 920, 150 905, 220 935 C 290 962, 350 960, 409 945 L409 1039 L0 1039 Z" fill="var(--teal-soft)"/>
    <path d="M0 950 C 80 930, 150 925, 220 955 C 290 985, 350 985, 409 968 L409 1039 L0 1039 Z" fill="var(--foam)"/>
    <path d="M0 968 C 80 950, 150 945, 220 975 C 290 1005, 350 1005, 409 990 L409 1039 L0 1039 Z" fill="var(--sand)"/>
  </svg>

  <div class="brand-dot"></div>
  <div class="brand-name">KORIVELL</div>

  <h1 class="product-title">AFTERSUN</h1>
  <p class="tagline">HYDRATE YOUR SKIN WITH THESE<br>ESSENTIAL INGREDIENTS</p>

  <div class="ingredient-pill" style="left:48px;top:706px;width:169px;"><span class="icon"></span>HYALURONATE ACID</div>
  <div class="ingredient-pill" style="left:228px;top:706px;width:131px;"><span class="icon"></span>CUCUMBER</div>
  <div class="ingredient-pill" style="left:50px;top:760px;width:88px;"><span class="icon"></span>ALOE</div>
  <div class="ingredient-pill" style="left:144px;top:760px;width:88px;"><span class="icon"></span>JOJOBA</div>
  <div class="ingredient-pill" style="left:242px;top:760px;width:118px;"><span class="icon"></span>SUNFLOWER</div>

  <div class="volume">3 FL OZ / 88 ML</div>
</section>

<section class="back-panel">
  <p class="copy-block" style="top:36px;">Preserve your skin and extend your tan with Calden Cove Korivell® AfterSun Moisturizing Lotion. Ultra moisturizing and soothing, it helps prevent peeling and dryness. Apply after the safest time to suntan, from 8am to about 11am and after 4pm, to keep your Korivell® looking rich, nourished and hydrated. Calden Cove Korivell® AfterSun Skin Moisturizing Lotion is a fast-absorbing formula designed to work immediately and restore essential moisture for healthier-looking skin. Clinically proven ingredients provide soothing and hydrating effects for up to 24 hours of luxurious moisturization. Now, after suntanning, your skin needs revitalization and hydration. Korivell® is enriched with soothing Jojoba, Aloe, Vitamin E, and Vitamin C, providing intense hydration to restore the skin's natural moisture balance. The lightweight, non-greasy formula absorbs quickly, leaving skin smooth and soft. Preserve your skin and extend your Korivell® with our ultra-moisturizing and soothing formula that helps prevent peeling and dryness. Apply after suntanning to keep your Korivell® looking rich and hydrated.</p>
  <p class="copy-block" style="top:286px;">Reef Friendly (made without oxybenzone or octinoxate)</p>

  <h2 class="copy-heading" style="top:333px;">Ingredients</h2>
  <p class="copy-block" style="top:362px;">Water, Caprylic/Capric Triglyceride, Petrolatum, Aloe Barbadensis Leaf Extract, Chamomilla Recutita (Matricaria) Flower Extract, Foeniculum Vulgare (Fennel) Seed Extract, Cucumis Sativus (Cucumber) Fruit Extract, Stearic Acid, Cetearyl Alcohol, Butyrospermum Parkii (Shea Butter), Glyceryl Stearate, PEG-100 Stearate, Dimethicone, Ethyl Hexyl Palmitate, Isopropyl Palmitate, Ascorbic Palmitate, Phenoxyethanol, Ethylhexylglycerin, Sodium Hyaluronate, Sodium Hydroxide, Carbomer, Helianthus Annuus (Sunflower) Seed Oil, FD&amp;C Blue No. 1, Simmondsia Chinensis (Jojoba) Seed Oil, Tocopheryl Acetate.</p>

  <h2 class="copy-heading" style="top:535px;">Directions</h2>
  <p class="copy-block" style="top:559px;">Smooth into skin as often as needed. Daily use will help prevent over-dry skin from recurring.</p>
  <p class="copy-block" style="top:600px;">This product is not tested on animals.</p>

  <h2 class="copy-heading" style="top:649px;">Warnings</h2>
  <p class="copy-block" style="top:668px;">For external use only. Do not use on damaged or broken skin. When using this product keep out of eyes. Rinse with water to remove. Stop use and ask a doctor if rash occurs. Keep out of reach of children. If product is swallowed, get medical help or contact a Poison Control Center right away. May stain some fabrics.</p>

  <h2 class="copy-heading" style="top:764px;">Other Information</h2>
  <p class="copy-block" style="top:784px;">Protect this product from excessive heat and sun.</p>

  <h2 class="copy-heading" style="top:828px;">Questions</h2>
  <p class="copy-block" style="top:848px;">questions@korivell.com</p>
</section>

</body>
</html>
```